Business card design for holistic health care clinic

We need a double-sided business card design for our holistic health care clinic that integrates our logo design and also its color scheme. My business is called Valmira. It is an integrative medicine clinic. You have already done the logo for me. Please ensure an elegant and upscale design that is not cluttered, but still has all the necessary information (please see below for details).

Target Market(s)

Wellness, fitness, rehabilitation for educated, well-traveled open-minded clients who are focused on natural, organic, balanced and preventive healthcare and lifestyle.

Industry/Entity Type

Medical

Contact Information for Business Card

Modern, clean.

Number of Pages Required

1 page

Font styles to use
Serif
Sans Serif

Colors

Designer to choose colors to be used in the design.

Requirements
Must have
• Logo on one side, all other information on the other side.
• Other information should include:
• Tobias Wrenfeld - DOE, CPT, LMT
• 4100 East Marrow Drive
• Austin, TX 78119
• 512 555 0148
• 818 555 0192
• info@ValmiraHealth.example
• t.wrenfeld@ValmiraHealth.example
Nice to have
• Darker background on front - but not totally black - shaded/dark gray.

```html
<!DOCTYPE html>
<html lang="en">
<head>
<meta charset="utf-8">
<title>Valmira – Business Card</title>
<link rel="stylesheet" href="https://fonts.googleapis.com/css2?family=Montserrat:wght@600;700&family=Nunito:wght@700&family=Work+Sans:wght@300;400&display=swap">
<style>
  :root {
    --brand-blue: #1a93d1;
    --ink: #3a3a3a;
    --ink-dark: #222;
    --card-light: #ffffff;
    --card-dark: #2a2a2a;
    --backdrop: #1d1d1d;
  }
  * { margin: 0; padding: 0; box-sizing: border-box; }
  html, body {
    width: 1200px; height: 930px; overflow: hidden;
    background: var(--backdrop);
  }
  .canvas { position: relative; width: 1200px; height: 930px; }

  .card {
    position: absolute; left: 278px; width: 644px; height: 368px;
    border-radius: 24px; overflow: hidden;
  }
  .card--info { top: 76px; background: var(--card-light); }
  .card--brand { top: 486px; background: var(--card-dark); }

  .wordmark {
    font-family: "Montserrat", sans-serif; font-weight: 700;
    color: var(--brand-blue); line-height: 1; letter-spacing: 1px;
    text-transform: uppercase;
  }
  .tagline {
    font-family: "Nunito", sans-serif; font-weight: 700;
    color: var(--brand-blue); line-height: 1;
  }

  .card--info .wordmark { position: absolute; left: 31px; top: 59px; font-size: 64px; }
  .card--info .tagline { position: absolute; left: 36px; top: 121px; font-size: 18px; }

  .holder__name {
    position: absolute; right: 35px; top: 150px;
    font-family: "Montserrat", sans-serif; font-weight: 600;
    font-size: 30px; color: var(--brand-blue); line-height: 1;
    text-transform: uppercase; letter-spacing: -0.5px; white-space: nowrap;
  }
  .holder__credentials {
    position: absolute; right: 35px; top: 185px;
    font-family: "Work Sans", sans-serif; font-weight: 400;
    font-size: 16px; color: var(--ink); line-height: 1; white-space: nowrap;
  }
  .rule {
    position: absolute; left: 34px; top: 191px; width: 456px; height: 2px;
    background: var(--brand-blue);
  }
  .edge-mark { position: absolute; right: 0; top: 156px; width: 20px; height: 42px; }
  .edge-mark::before {
    content: ""; position: absolute; left: 0; top: 0; width: 4px; height: 100%;
    background: var(--ink-dark);
  }
  .edge-mark::after {
    content: ""; position: absolute; right: 0; top: 0; width: 12px; height: 100%;
    background: var(--brand-blue);
  }

  .address, .contacts {
    position: absolute; left: 34px;
    font-family: "Work Sans", sans-serif; font-weight: 300;
    font-size: 16.5px; color: var(--ink); line-height: 20px; list-style: none;
    font-style: normal;
  }
  .address { top: 218px; }
  .contacts { top: 267px; }
  .contacts li { display: flex; align-items: center; height: 20px; }
  .contacts svg { width: 11px; height: 11px; margin-right: 9px; flex: none; }

  .card--brand .brand-lockup {
    position: absolute; left: 0; right: 0; top: 152px; text-align: center;
  }
  .card--brand .wordmark { font-size: 88px; }
  .card--brand .tagline { font-size: 25px; margin-top: 10px; }
</style>
</head>
<body>
<main class="canvas">

  <section class="card card--info" aria-label="Card side with contact details">
    <div class="wordmark">Valmira</div>
    <div class="tagline">Integrative Holistic Medicine</div>

    <div class="holder__name">Tobias Wrenfeld</div>
    <div class="rule"></div>
    <div class="holder__credentials">DOE, CPT, LMT</div>
    <div class="edge-mark"></div>

    <address class="address">
      4100 East Marrow Drive<br>Austin, TX 78119
    </address>

    <ul class="contacts">
      <li>
        <svg viewBox="0 0 12 12" fill="none" stroke="var(--brand-blue)" stroke-width="1.4"><path d="M3 1.5l1.6 2.3-1 1.1c.7 1.4 1.8 2.5 3.2 3.2l1.1-1 2.3 1.6-.9 1.6C6 10 2 6 1.7 2.4z"/></svg>
        512 555 0148
      </li>
      <li>
        <svg viewBox="0 0 12 12" fill="none" stroke="var(--brand-blue)" stroke-width="1.4"><rect x="3" y="1" width="6" height="10" rx="1"/><line x1="5" y1="9" x2="7" y2="9"/></svg>
        818 555 0192
      </li>
      <li>
        <svg viewBox="0 0 12 12" fill="none" stroke="var(--brand-blue)" stroke-width="1.3"><rect x="1" y="2.5" width="10" height="7"/><path d="M1 2.5l5 4 5-4"/></svg>
        info@ValmiraHealth.example
      </li>
      <li>
        <svg viewBox="0 0 12 12" fill="none" stroke="var(--brand-blue)" stroke-width="1"><circle cx="6" cy="6" r="5"/><ellipse cx="6" cy="6" rx="2.2" ry="5"/><line x1="1" y1="6" x2="11" y2="6"/><path d="M2 3.5h8M2 8.5h8"/></svg>
        t.wrenfeld@ValmiraHealth.example
      </li>
    </ul>
  </section>

  <section class="card card--brand" aria-label="Card side with brand name">
    <div class="brand-lockup">
      <div class="wordmark">Valmira</div>
      <div class="tagline">Integrative Holistic Medicine</div>
    </div>
  </section>

</main>
</body>
</html>
```